Large online photo magazine needs redesign

We have previously digitised a historical photographic magazine of around 20,000 printed pages and made it available online. The magazine ran up to the early 1970s, and the content is largely black and white photographs of local events, accompanied by short captions.

Although the content is very rich, the design needs to be revisited so that:
* it is visually appealing
* it is responsive (i.e. works in browsers across all manner of devices)
* is faithful to the nature of the content

There are only a few core page types, and the central one is the article page, an example of which can be seen at:
http://snapgazette.example/gisborne/issue/KLR48_19600714/t1-body-d4.html

Any design submitted should be based on the treatment of an article page such as the above.

Given the large number of pages on our site, we need a design which can be templated to work for any content in the collection, i.e. we cannot hand-craft our templates to match a given page of content, rather a template must work acceptably well for all content.

The current site, although basic in design, has the advantage that it is quite efficient in the amount of data per page request (around 100k - 200k). While not adverse to web fonts, banner imagery etc, we will carefully consider the benefit gained from any such treatment against the amount of extra data that needs to be downloaded to the client's browser.

For the right design, we are able ourselves to adapt it to a CSS layout.

An example of each core page type is as follows (though for this project we only expect a design for a single page, as itemised above):

http://snapgazette.example/gisborne/index.html
http://snapgazette.example/gisborne/about.html
http://snapgazette.example/gisborne/help.html
http://snapgazette.example/gisborne/initial/index.html
http://snapgazette.example/gisborne/search/results?type=section&text=smith&cmdSubmit=Go
http://snapgazette.example/gisborne/advanced-search/index.html
http://snapgazette.example/gisborne/issue/KLR48_19600714/t1-front-d1.html
http://snapgazette.example/gisborne/issue/KLR48_19600714/index.html
http://snapgazette.example/gisborne/issue/KLR48_19600714/fig-KLR48_19600714_005a.html
http://snapgazette.example/gisborne/issue/KLR48_19600714/KLR48_19600714_012.html
http://snapgazette.example/gisborne/issue/KLR48_19600714/thumbnails.html

Target Market(s)

A general browsing audience of all ages, but skewed towards the older generations, and those interested in family / regional history.

The average user will not be particularly web-savy, and the treatment of the content should not detract / distract from the actual content itself.

Industry/Entity Type

Events

Requirements
Must have
• * it is visually appealing
The content should be visually appealing to the audience, which can be defined as a general browsing audience of all ages, but skewed towards the middle and older generations.

* it is responsive (the design can be adapted - by us - to work in browsers across all manner of devices)

The magazine covers (http://snapgazette.example/gisborne/issues/index.html) offer some possible inspiration for treatment of the material.

```html
<!DOCTYPE html>
<html lang="en">
<head>
<meta charset="utf-8">
<title>Snap Gazette — Flying Sisters from Gisborne</title>
<link rel="stylesheet" href="https://fonts.googleapis.com/css2?family=Open+Sans:wght@400;600;700&family=Courier+Prime:wght@400;700&display=swap">
<style>
:root{
  --red:#cb3a55;
  --red-dark:#a92c44;
  --bar:#505050;
  --ink:#333;
  --muted:#666;
  --line:#e6e6e6;
  --grey-btn:#d6d6d6;
  --paper:#d9d2bd;
  --paper-light:#ebe6d6;
  --print:#2e2c28;
}
*{box-sizing:border-box;margin:0;padding:0}
html,body{width:1014px;height:1200px;overflow:hidden;background:#fff;font-family:"Open Sans",Arial,sans-serif;color:var(--ink)}
a{color:inherit;text-decoration:none}
.topbar{height:26px;background:var(--bar);color:#fff;font-size:10px;display:flex;align-items:center;justify-content:space-between;padding:0 40px 0 91px}
.topbar .login{display:flex;align-items:center;gap:8px}
.masthead{margin:8px 7px 0;height:96px;background:#fafafa;position:relative}
.brand{position:absolute;left:73px;top:13px;width:537px;height:66px;background:var(--red);display:flex;align-items:center;justify-content:center;color:#fff;font-weight:700;font-size:36px;letter-spacing:3px;text-transform:uppercase}
.nav{height:46px;border-bottom:1px solid var(--line);box-shadow:0 2px 3px rgba(0,0,0,.05);display:flex;align-items:center;padding-left:82px;position:relative;font-size:14.5px;color:#444}
.nav .home{width:40px;height:46px;display:flex;align-items:center;justify-content:center;border-bottom:3px solid var(--red)}
.nav .menu{margin:0 20px 0 14px}
.nav a.item{margin-right:32px}
.nav .search{position:absolute;right:60px;top:0;height:46px;display:flex;align-items:center;gap:12px;color:var(--red);font-size:12.5px}

.feature{position:absolute;left:79px;top:218px;width:853px;height:385px;display:flex}
.spread{width:593px;height:385px;border:2px solid var(--red);background:linear-gradient(90deg,#cfc7af,var(--paper-light) 46%,#b9b19a 49.5%,var(--paper-light) 53%,var(--paper));position:relative;overflow:hidden}
.spread .tile{position:absolute;border:1px solid #6d6a62}
.tone-a{background:radial-gradient(ellipse at 35% 40%,#c9c7c1,#6e6c66 60%,#2f2e2b)}
.tone-b{background:radial-gradient(ellipse at 60% 45%,#d4d2cc,#7a7872 55%,#3a3936)}
.tone-c{background:linear-gradient(160deg,#a9a7a1,#4a4945 70%,#262523)}
.tone-d{background:linear-gradient(180deg,#d6d5d0,#8f8e88 45%,#3b3a37 55%,#cfcdc5)}
.tone-e{background:linear-gradient(90deg,#3b3a37,#6a6964 50%,#2c2b29)}
.spread .copy{position:absolute;font-family:"Courier Prime",monospace;font-size:5.6px;line-height:7px;color:var(--print);text-align:justify}
.spread .copy b{font-size:10px;line-height:12px;display:block;font-weight:700;text-align:left}
.spread .copy i{font-family:"Open Sans",sans-serif;font-size:10px;display:block;margin-bottom:2px}
.spread .dots{position:absolute;left:296px;bottom:3px;width:48px;height:22px;background:#fff;display:flex;justify-content:space-around;align-items:center;font-size:10px;color:#888}

.panel{flex:1;background:var(--red);color:#fff;padding:26px 4px 0 19px;position:relative}
.panel h1{font-size:19px;font-weight:600;line-height:21px;text-transform:uppercase}
.panel p{font-size:11.4px;line-height:16px;margin-top:27px}
.panel .issue{font-size:18px;font-weight:600;margin-top:44px}
.panel .arrows{position:absolute;left:74px;top:281px;display:flex;gap:2px}
.panel .arrows span{width:62px;height:62px;background:var(--grey-btn);display:flex;align-items:center;justify-content:center}

.latest{position:absolute;left:82px;top:644px;width:850px;height:28px;border-bottom:2px solid var(--red)}
.latest h2{display:inline-block;background:var(--red);color:#fff;font-size:13.5px;font-weight:700;padding:4px 4px;height:26px}
.latest .ctl{position:absolute;right:0;top:6px;display:flex;gap:14px}

.cards{position:absolute;left:67px;top:704px;width:884px;display:flex;gap:36px}
.card{width:271px;font-size:12.2px;color:var(--muted);position:relative;height:300px}
.card .photo{height:162px;border:1px solid #999;position:relative;overflow:hidden}
.card .photo span{position:absolute;display:block}
.card .date{font-size:11px;margin-top:26px}
.card .text{margin-top:11px;line-height:15px;text-align:justify;letter-spacing:-.15px}
.card .text strong{font-weight:400;text-transform:uppercase;display:block;text-align:left}
.card .more{position:absolute;right:0;top:304px;color:var(--red);font-size:12.8px}

.partners{position:absolute;left:0;top:1029px;width:1014px;height:125px;border-top:3px solid var(--red);display:flex;justify-content:center;align-items:center;gap:18px;font-size:12px;font-weight:700;color:#333}
.partners .sq{width:12px;height:12px;background:#c9a23a;display:inline-block;margin-right:5px;vertical-align:middle}
.partners .red{color:var(--red-dark)}
.footer{position:absolute;left:0;top:1159px;width:1014px;height:41px;background:var(--bar);color:#fff;font-size:9.5px;padding:12px 80px 0 82px;display:flex;justify-content:space-between}
.footer .code{position:absolute;right:12px;bottom:6px;font-size:8.5px}
</style>
</head>
<body>
<header class="topbar">
  <div><a href="#">Advanced Search</a> | <a href="#">Help</a> | <a href="#">Report an error</a></div>
  <div class="login">Login
    <svg width="11" height="13" viewBox="0 0 11 13"><circle cx="5.5" cy="3.5" r="3" fill="#fff"/><path d="M0 13c0-4 2.5-5.5 5.5-5.5S11 9 11 13z" fill="#fff"/></svg>
  </div>
</header>
<div class="masthead"><div class="brand">Snap Gazette</div></div>
<nav class="nav">
  <a class="home" href="#"><svg width="18" height="18" viewBox="0 0 18 18"><path d="M9 1 0 9h2.5v8h5v-5h3v5h5V9H18z" fill="#444"/></svg></a>
  <span class="menu"><svg width="17" height="13" viewBox="0 0 17 13"><rect width="17" height="2.2" fill="#444"/><rect y="5.4" width="17" height="2.2" fill="#444"/><rect y="10.8" width="17" height="2.2" fill="#444"/></svg></span>
  <a class="item" href="#">About Us</a>
  <a class="item" href="#">Browse Snap Gazette</a>
  <a class="item" href="#">A-Z People</a>
  <div class="search">Search Snap Gazette
    <svg width="15" height="15" viewBox="0 0 15 15"><circle cx="6" cy="6" r="4.7" fill="none" stroke="#444" stroke-width="2"/><path d="m9.5 9.5 4.5 4.5" stroke="#444" stroke-width="2.2"/></svg>
  </div>
</nav>

<section class="feature">
  <div class="spread">
    <div class="tile tone-a" style="left:2px;top:2px;width:133px;height:118px" role="img" aria-label="Engagement portrait of a young couple"></div>
    <div class="copy" style="left:150px;top:18px;width:125px"><i>Engaged</i>Nola Brent, daughter of Mr and Mrs R. Brent, Gisborne, to Alan Ferris, son of Mr and Mrs T. Ferris, Napier. Also Mary Dunn to Ken Hales, both of this city.</div>
    <div class="tile tone-b" style="left:3px;top:128px;width:127px;height:124px" role="img" aria-label="Portrait of a young woman"></div>
    <div class="tile tone-c" style="left:136px;top:126px;width:146px;height:124px" role="img" aria-label="Portraits of two men and a woman in glasses"></div>
    <div class="tile tone-b" style="left:3px;top:258px;width:82px;height:112px" role="img" aria-label="Portrait of a young woman"></div>
    <div class="copy" style="left:95px;top:254px;width:96px">Engaged: Joy Marsh to Peter Lane; Ruth Hale to Colin Dent, both of Gisborne.</div>
    <div class="tile tone-a" style="left:205px;top:255px;width:72px;height:112px" role="img" aria-label="Portrait of a young woman"></div>

    <div class="tile tone-c" style="left:298px;top:2px;width:186px;height:140px" role="img" aria-label="Three sisters in air hostess uniforms"></div>
    <div class="tile tone-e" style="left:497px;top:2px;width:84px;height:202px" role="img" aria-label="Air hostess standing in an aircraft doorway"></div>
    <div class="copy" style="left:304px;top:150px;width:186px"><b>Flying Sisters from Gisborne</b>This is probably something of a record--three sisters who are all air hostesses. They are the Harlow sisters, daughters of Mr and Mrs W. G. Harlow.</div>
    <div class="tile tone-d" style="left:302px;top:212px;width:268px;height:110px" role="img" aria-label="Old highway bridge across a wide river"></div>
    <div class="copy" style="left:304px;top:326px;width:264px"><b style="font-size:6px;line-height:8px;letter-spacing:2px">BRIDGE IN SPLINTS</b>The old highway bridge across the river has more Bailey splints than any other bridge in the country.</div>
    <div class="dots"><span>‹</span><span>›</span></div>
  </div>
  <div class="panel">
    <h1>Flying Sisters from Gisborne</h1>
    <p>This is probably something of a record--three sisters who are all air hostesses. They are the Harlow sisters.....Maribel, Ottilie, and Rosanne, daughters of Mr and Mrs W. G. Harlow, Kel-more Road, Gisborne.</p>
    <div class="issue">No 73 JULY 14, 1965</div>
    <div class="arrows">
      <span><svg width="12" height="18" viewBox="0 0 12 18"><path d="M10 2 3 9l7 7" fill="none" stroke="#fff" stroke-width="3"/></svg></span>
      <span><svg width="12" height="18" viewBox="0 0 12 18"><path d="m2 2 7 7-7 7" fill="none" stroke="#fff" stroke-width="3"/></svg></span>
    </div>
  </div>
</section>

<div class="latest">
  <h2>Latest Articles</h2>
  <div class="ctl">
    <svg width="8" height="12" viewBox="0 0 8 12"><path d="M6 1 1 6l5 5" fill="none" stroke="#aaa" stroke-width="1.5"/></svg>
    <svg width="8" height="12" viewBox="0 0 8 12"><path d="m2 1 5 5-5 5" fill="none" stroke="#333" stroke-width="1.5"/></svg>
  </div>
</div>

<section class="cards">
  <article class="card">
    <div class="photo tone-c" role="img" aria-label="Photograph of three air hostesses in uniform caps"></div>
    <div class="date">No 73 July 14, 1960</div>
    <div class="text">This is probably something of a record--three sisters who are all air hostesses. They are the Harlow sisters.....Maribel, Ottilie, and Rosanne, daughters of Mr and Mrs W. G. Harlow, Kel-more Road, Gisborne.</div>
    <a class="more" href="#">Read more</a>
  </article>
  <article class="card">
    <div class="photo tone-e" role="img" aria-label="Photograph of an air hostess standing in an aircraft doorway"></div>
    <div class="date">No 73 July 14, 1960</div>
    <div class="text">And this young lady, Edith Carrow, of Auckland, has made history in another way. She was the first air hostess to make a scheduled flight to Gisborne, on Sunday of last week. Hostess ser-vice has been extended by S.A.L....</div>
    <a class="more" href="#">Read more</a>
  </article>
  <article class="card">
    <div class="photo tone-d" role="img" aria-label="Photograph of an old highway bridge across a river with its printed caption">
      <span style="left:100px;right:4px;bottom:4px;height:36px;background:var(--paper-light)"></span>
    </div>
    <div class="date">No 73 July 14, 1960</div>
    <div class="text"><strong>Bridge in splints</strong>The old highway bridge across the Waiapu River near Ruatoria probably has more Bailey "splints" than any other bridge in the country. It is to be replaced soon by ...</div>
    <a class="more" href="#">Read more</a>
  </article>
</section>

<section class="partners">
  <span><span class="sq"></span>Harwood Library</span>
  <span>Reading Fund Trust</span>
  <span>Eastbay District Council</span>
  <span>Northgate Trust</span>
  <span class="red">Elsie Ranfield Trust</span>
  <span>pageDigital</span>
</section>
<footer class="footer">
  <div>© 2012 Harwood Memorial Library</div>
  <div>Disclaimer | Privacy | Advertisement | About Us</div>
  <span class="code">Z12</span>
</footer>
</body>
</html>
```